Business card design for a dynamic IT consulting company

We need a business card design for a young firm, specialized in the Telecommunications/Consulting industry. The name of the company is Quindor and Partners Business Consulting Ltd. (Short name: Quindor and Partnes)
Quindor = solve read reverse, so we aim to be uncomplicated and solution-oriented. The small pipe in our logo is also related to the word solve. So we need a new business card design, which is simple, eye catching and something non traditional (I would probably prefer a square shaped design rather than a rectangle, but open for suggestions). Attached our logo.

Target Market(s)

Usually our customers are Tier1 Telecoms providers (Q-Netra, Palorix, etc) and their executives.

Industry/Entity Type

Business

Contact Information for Business Card

Name: Bence Tolnavari
Email: b.tolnavari@quindor.hu
Web: www.quindor.hu
Mobile: +36 30 518 2769
Title: Managing Director

Optional:
Company name: Quindor and Partners Ltd.
Address: 1087 Budapest, Tolvenka str. 28/C, Hungary

Font styles to use
Other font styles liked:
• helveticaneue_medium, Prime Regular are used now.

Colors

Designer to choose colors to be used in the design.

Requirements
Must have
• I would like to have a 2 sided design.
Nice to have
• I thought if we make the logo a bit bigger (without the company name), that could go to the back with the company name below. I though, if the pipe in the logo is somehow touchable on the business card, would be nice and unique.

```html
<!DOCTYPE html>
<html lang="en">
<head>
<meta charset="utf-8">
<title>Quindor and Partners – Business Card</title>
<link rel="stylesheet" href="https://fonts.googleapis.com/css2?family=Roboto:wght@300;400;500&display=swap">
<style>
  :root {
    --page-bg: #1b1b1b;
    --card-bg: #2b2b2b;
    --card-edge: #29b6e6;
    --text-light: #d9d9d9;
    --accent-blue: #1f8fd1;
    --divider: #1c6a9a;
  }
  * { margin: 0; padding: 0; box-sizing: border-box; }
  html, body {
    width: 1000px;
    height: 1200px;
    overflow: hidden;
    background: var(--page-bg);
    font-family: "Roboto", "Helvetica Neue", Arial, sans-serif;
  }
  .sheet {
    width: 1000px;
    height: 1200px;
    display: grid;
    grid-template-rows: 600px 600px;
  }
  .slot {
    display: flex;
    align-items: center;
    justify-content: center;
  }
  .card {
    position: relative;
    width: 760px;
    height: 434px;
    background: var(--card-bg);
    border-bottom: 4px solid var(--card-edge);
    border-left: 4px solid var(--card-edge);
  }

  /* Front side */
  .card-front .identity {
    position: absolute;
    left: 120px;
    top: 215px;
  }
  .identity .person-name {
    color: var(--text-light);
    font-size: 21px;
    font-weight: 400;
    letter-spacing: 0.2px;
  }
  .identity .person-title {
    color: var(--accent-blue);
    font-size: 15px;
    font-weight: 400;
    margin-top: 3px;
  }
  .card-front .divider {
    position: absolute;
    left: 385px;
    top: 120px;
    width: 1px;
    height: 200px;
    background: var(--divider);
  }
  .contact-list {
    position: absolute;
    left: 425px;
    top: 140px;
    list-style: none;
  }
  .contact-list li {
    display: flex;
    align-items: center;
    gap: 10px;
    color: var(--text-light);
    font-size: 15px;
    font-weight: 300;
    height: 30px;
  }
  .contact-list svg {
    width: 14px;
    height: 14px;
    flex: none;
  }

  /* Back side */
  .card-back .brand {
    position: absolute;
    left: 0;
    right: 0;
    top: 0;
    bottom: 0;
    display: flex;
    align-items: center;
    justify-content: center;
    gap: 16px;
  }
  .brand .brand-square {
    width: 22px;
    height: 22px;
    background: var(--accent-blue);
  }
  .brand .brand-name {
    color: var(--text-light);
    font-size: 44px;
    font-weight: 400;
    letter-spacing: 0.5px;
  }
</style>
</head>
<body>
<main class="sheet">
  <section class="slot">
    <article class="card card-front">
      <div class="identity">
        <p class="person-name">Bence Tolnavari</p>
        <p class="person-title">Managing Director</p>
      </div>
      <div class="divider"></div>
      <ul class="contact-list">
        <li>
          <svg viewBox="0 0 14 14" aria-hidden="true"><rect x="3.5" y="0.75" width="7" height="12.5" rx="1.2" fill="none" stroke="var(--accent-blue)" stroke-width="1.2"/><line x1="6" y1="11" x2="8" y2="11" stroke="var(--accent-blue)" stroke-width="1"/></svg>
          <span>+36 30 518 2769</span>
        </li>
        <li>
          <svg viewBox="0 0 14 14" aria-hidden="true"><rect x="0.75" y="2.75" width="12.5" height="8.5" fill="none" stroke="var(--accent-blue)" stroke-width="1.2"/><polyline points="0.75,2.75 7,7.5 13.25,2.75" fill="none" stroke="var(--accent-blue)" stroke-width="1.2"/></svg>
          <span>b.tolnavari@quindor.hu</span>
        </li>
        <li>
          <svg viewBox="0 0 14 14" aria-hidden="true"><circle cx="7" cy="7" r="6" fill="none" stroke="var(--accent-blue)" stroke-width="1.2"/><ellipse cx="7" cy="7" rx="2.6" ry="6" fill="none" stroke="var(--accent-blue)" stroke-width="1"/><line x1="1" y1="7" x2="13" y2="7" stroke="var(--accent-blue)" stroke-width="1"/></svg>
          <span>www.quindor.hu</span>
        </li>
      </ul>
    </article>
  </section>
  <section class="slot">
    <article class="card card-back">
      <div class="brand">
        <span class="brand-square"></span>
        <span class="brand-name">Quindor &amp; Partners</span>
      </div>
    </article>
  </section>
</main>
</body>
</html>
```